Word Template Designs for Offensive Security Professional Services Report

We need a Microsoft Word Template designed for our Offensive Security professional services reports which includes the following services:

RedTeaming
Network Penetration Testing
Web Application Penetration Testing
Wireless Penetration Testing
Social Engineering

The templates should include the following:
Cover Page design with our Logo included
Executive Summary Page design
Detailed Findings Page design
Design for Last Page

Lastly, I would also like a template I can use for all of my Statements of Work

Requirements
Must have
• Beautiful Eye Catching HD pictures that represent my Offensive Security projects
The design should flow well with our logo

```html
<!DOCTYPE html>
<html lang="en">
<head>
<meta charset="utf-8">
<title>Northgate Assurance – Scope of Work Template Pages</title>
<link href="https://fonts.googleapis.com/css2?family=Montserrat:wght@400;600;700;800&family=Open+Sans:wght@400;600;700&display=swap" rel="stylesheet">
<style>
:root{
  --stage:#4a4a4a;
  --paper:#ffffff;
  --ink:#2b2b2b;
  --muted:#6f6f6f;
  --rule:#d9d9d9;
  --green:#7cb342;
  --green-dark:#4e7a22;
  --deep:#0f2a1a;
}
*{box-sizing:border-box;margin:0;padding:0}
html,body{width:1200px;height:3000px;overflow:hidden;background:var(--stage)}
body{font-family:"Open Sans",Arial,sans-serif;color:var(--ink);position:relative}
.page{position:absolute;width:432px;height:560px;background:var(--paper);padding:34px 34px 28px;overflow:hidden;box-shadow:0 2px 6px rgba(0,0,0,.35)}
.col-l{left:150px}.col-r{left:618px}
.r1{top:40px}.r2{top:630px}.r3{top:1220px}.r4{top:1810px}.r5{top:2400px}
.page-title{font-family:"Montserrat",Arial,sans-serif;font-weight:800;font-size:21px;letter-spacing:.5px;color:var(--ink);margin-bottom:12px;text-transform:uppercase}
.page-title span{color:var(--green)}
.sub{font-family:"Montserrat",Arial,sans-serif;font-weight:700;font-size:8px;text-transform:uppercase;color:var(--ink);margin:10px 0 4px}
.sub span{color:var(--green)}
p{font-size:5.4px;line-height:1.55;color:var(--muted);margin-bottom:5px}
ul,ol{font-size:5.4px;line-height:1.6;color:var(--muted);padding-left:12px;margin-bottom:5px}
li::marker{color:var(--green)}
.footer{position:absolute;left:34px;right:34px;bottom:14px;display:flex;justify-content:space-between;font-size:5px;color:var(--muted);border-top:1px solid var(--rule);padding-top:4px}
.footer b{color:var(--green);font-weight:600}
/* cover */
.brand{font-family:"Montserrat",Arial,sans-serif;font-weight:700;font-size:10px;color:var(--ink);letter-spacing:.3px}
.cover-title{font-family:"Montserrat",Arial,sans-serif;font-weight:700;font-size:12px;line-height:1.3;color:var(--green-dark);margin-top:46px;width:190px}
.cover-title strong{display:block;color:var(--green);font-size:11px;text-transform:uppercase;margin-bottom:2px}
.prep{font-family:"Montserrat",Arial,sans-serif;font-size:8px;font-weight:700;color:var(--green-dark);margin-top:12px}
.prep small{display:block;font-size:7px;color:var(--ink);font-weight:600}
.prep-by{position:absolute;left:34px;top:350px;font-size:5.4px;line-height:1.6;color:var(--muted)}
.prep-by b{font-family:"Montserrat",Arial,sans-serif;color:var(--green-dark);font-size:7px;display:block}
.cover-art{position:absolute;right:0;top:150px;width:250px;height:330px;background:radial-gradient(circle at 55% 45%,#9be15d 0%,#3f8f3a 25%,#14402a 60%,var(--deep) 100%)}
.cover-band{position:absolute;left:0;right:0;bottom:0;height:40px;background:linear-gradient(90deg,#14402a,#3f8f3a)}
/* table */
.rev{width:100%;border-collapse:collapse;font-size:5.4px;margin-top:8px}
.rev th{background:var(--green);color:#fff;font-weight:600;padding:4px;text-align:left}
.rev td{border-bottom:1px solid var(--rule);padding:4px;color:var(--muted)}
.toc{padding:0}
.toc li{list-style:none;display:flex;font-size:5.6px;color:var(--ink);border-bottom:1px dotted var(--rule);padding:3px 0}
.toc li span:first-child{flex:1;font-weight:600;text-transform:uppercase}
.twocol{display:grid;grid-template-columns:1fr 1fr;gap:0 10px}
.sign{display:flex;flex-direction:column;align-items:flex-end;gap:8px;margin-top:14px;font-size:5.4px;color:var(--muted)}
.sign div{width:150px;border-bottom:1px solid var(--ink);padding-bottom:1px}
</style>
</head>
<body>

<!-- Cover -->
<section class="page col-l r1">
  <div class="brand">Northgate Assurance</div>
  <h1 class="cover-title"><strong>Scope of Work:</strong>External, Internal Network, Wireless and Web Application Penetration Testing Engagement</h1>
  <div class="prep">PREPARED FOR<small>[Client Name]</small></div>
  <div class="prep-by"><b>PREPARED BY</b>Northgate Assurance Security Services<br>Lead Consultant: Jordan Avery<br>Phone: +1 (555) 014 2290<br>Email: contact@northgateassurance.example<br>Web: northgateassurance.example</div>
  <div class="cover-art" role="img" aria-label="Green glowing circuit board with security shield motif"></div>
  <div class="cover-band"></div>
</section>

<!-- Scope approval -->
<section class="page col-r r1">
  <h2 class="page-title">Scope <span>Approval</span></h2>
  <div class="sub">Client Activity <span>Checklist</span></div>
  <ul>
    <li>Provide a list of external IP ranges and domains in scope.</li>
    <li>Confirm internal network segments and access method.</li>
    <li>Share wireless SSIDs and site locations to be assessed.</li>
    <li>Provide web application URLs and test user accounts for each role.</li>
    <li>Nominate a technical contact available during all testing windows.</li>
    <li>Notify hosting providers and third parties of planned testing activity.</li>
    <li>Confirm testing windows, blackout periods and emergency contacts.</li>
  </ul>
  <p>Please review each item carefully. Any change to scope after approval may affect the timeline and the final price of the engagement.</p>
  <ul>
    <li>Confirm the engagement objectives with key stakeholders.</li>
    <li>Agree on the report format and the delivery schedule.</li>
    <li>Approve the rules of engagement and data handling terms.</li>
  </ul>
  <p>By signing below, the client confirms that the scope described in this document is accurate and that all listed systems are owned or authorised for testing. Northgate Assurance will begin work once the signed approval is received.</p>
  <p>Any findings that pose an immediate risk will be reported to the nominated contact without delay, ahead of the final report.</p>
  <div class="sign"><div>Signature:</div><div>Name:</div><div>Date:</div></div>
  <div class="footer"><span>Page 2</span><b>northgateassurance.example</b></div>
</section>

<!-- Revision control -->
<section class="page col-l r2">
  <h2 class="page-title">Document Revision <span>Control</span></h2>
  <table class="rev">
    <tr><th>Revision Number</th><th>Date</th><th>Revised by</th><th>Notes</th></tr>
    <tr><td>1.0</td><td>DD/MM/YYYY</td><td>J. Avery</td><td>Initial draft</td></tr>
  </table>
  <div class="footer"><span>Page 3</span><b>northgateassurance.example</b></div>
</section>

<!-- Table of contents -->
<section class="page col-r r2">
  <h2 class="page-title">Table of <span>Contents</span></h2>
  <ul class="toc">
    <li><span>Scope Approval</span><span>2</span></li>
    <li><span>Document Revision Control</span><span>3</span></li>
    <li><span>Proposal Summary</span><span>5</span></li>
    <li><span>Engagement Overview</span><span>5</span></li>
    <li><span>Phase One: External Network Testing</span><span>5</span></li>
    <li><span>Phase Two: Internal Network Testing</span><span>5</span></li>
    <li><span>Phase Three: Wireless Testing</span><span>6</span></li>
    <li><span>Phase Four: Web Application Testing</span><span>6</span></li>
    <li><span>Engagement Deliverables</span><span>6</span></li>
    <li><span>Phase Specific Tasks</span><span>7</span></li>
    <li><span>Client Obligations</span><span>8</span></li>
    <li><span>Meeting Workshop</span><span>8</span></li>
    <li><span>Pricing Schedule</span><span>10</span></li>
  </ul>
  <div class="footer"><span>Page 4</span><b>northgateassurance.example</b></div>
</section>

<!-- Proposal summary -->
<section class="page col-l r3">
  <h2 class="page-title">Proposal <span>Summary</span></h2>
  <p>Northgate Assurance is pleased to present this proposal for a penetration testing engagement. The work will identify weaknesses across external, internal, wireless and web application environments and provide clear guidance to reduce risk.</p>
  <div class="sub">Engagement <span>Overview</span></div>
  <p>The engagement is split into four phases. Each phase uses a proven method combining automated tools and manual testing by experienced consultants. Results from every phase are combined into one report with ranked findings.</p>
  <p>Testing will be performed from the viewpoint of an outside attacker and of an insider with standard access, giving a full picture of the current security posture.</p>
  <ul><li>External Network Penetration Testing</li><li>Internal Network Penetration Testing</li><li>Wireless and Web Application Penetration Testing</li></ul>
  <div class="sub">Phase One: <span>External Network Penetration Testing</span></div>
  <p>This phase reviews all internet facing systems to find services, weak settings and known flaws that an attacker could use to gain a foothold inside the network.</p>
  <p>Discovery, enumeration and exploitation will be performed within the agreed rules of engagement.</p>
  <div class="sub">Phase Two: <span>Internal Network Penetration Testing</span></div>
  <p>This phase simulates an attacker who has gained access to the internal network. Consultants will attempt to move laterally, escalate privileges and reach critical data.</p>
  <p>Active Directory, file shares, and core servers will be reviewed for weak controls.</p>
  <div class="footer"><span>Page 5</span><b>northgateassurance.example</b></div>
</section>

<section class="page col-r r3">
  <div class="sub">Phase Three: <span>Wireless Penetration Testing</span></div>
  <p>Wireless networks at the agreed sites will be assessed for weak encryption, rogue access points and poor segmentation between guest and corporate networks.</p>
  <p>Consultants will attempt to capture and crack credentials and bypass network access controls.</p>
  <div class="sub">Phase Four: <span>Web Application Penetration Testing</span></div>
  <p>Each web application in scope will be tested against current industry guidance, covering authentication, session handling, input validation, access control and business logic.</p>
  <p>Testing is performed with and without valid accounts to measure the impact of each role.</p>
  <p>Findings will be confirmed manually to remove false positives before they are reported.</p>
  <div class="sub">Engagement <span>Deliverables</span></div>
  <p>At the end of the engagement the client will receive:</p>
  <div class="twocol">
    <ul><li>Executive summary</li><li>Technical findings</li><li>Risk ratings</li><li>Evidence screenshots</li><li>Remediation steps</li></ul>
    <ul><li>Attack path overview</li><li>Scope summary</li><li>Tool listing</li><li>Retest guidance</li><li>Debrief session</li></ul>
  </div>
  <ul><li>A draft report for review within five working days.</li><li>A final report issued after client comments are received.</li></ul>
  <div class="footer"><span>Page 6</span><b>northgateassurance.example</b></div>
</section>

<!-- Phase specific tasks -->
<section class="page col-l r4">
  <h2 class="page-title">Phase Specific <span>Tasks</span></h2>
  <div class="sub">Phase One: <span>External Network Penetration Testing</span></div>
  <ol>
    <li>Kick-off call to confirm scope and contacts.</li>
    <li>Passive reconnaissance of public records and domains.</li>
    <li>Port and service discovery on all in-scope addresses.
      <ul><li>TCP and UDP scanning</li><li>Service version detection</li></ul></li>
    <li>Vulnerability identification and manual validation.</li>
    <li>Exploitation of confirmed issues within agreed limits.
      <ul><li>Credential attacks on exposed services</li><li>Testing of remote access portals</li></ul></li>
    <li>Review of mail, DNS and certificate settings.</li>
    <li>Collection of evidence for each finding.</li>
    <li>Immediate notice of any critical issue.</li>
    <li>Clean up of any test artefacts.
      <ul><li>Removal of uploaded files</li><li>Closing of test sessions</li></ul></li>
    <li>Draft findings for the phase report.</li>
    <li>Internal quality review of results.</li>
    <li>Hand over to the reporting team.</li>
  </ol>
  <div class="footer"><span>Page 7</span><b>northgateassurance.example</b></div>
</section>

<section class="page col-r r4">
  <div class="sub">Client <span>Obligations</span></div>
  <p>The client will provide timely access to systems, accounts and staff needed for testing, and will ensure that backups are in place before work begins.</p>
  <p>The client will inform Northgate Assurance of any planned changes during the testing window.</p>
  <div class="sub">Meeting <span>Workshop</span></div>
  <ul><li>A closing workshop will walk through all key findings with the client team.</li><li>Questions on remediation will be answered during the session.</li></ul>
  <div class="footer"><span>Page 8</span><b>northgateassurance.example</b></div>
</section>

<!-- Continued tasks -->
<section class="page col-l r5">
  <div class="sub">Phase Two: <span>Internal Network Penetration Testing</span></div>
  <ol>
    <li>Connect test device to the agreed network segment.</li>
    <li>Discover live hosts and network services.
      <ul><li>Host enumeration</li><li>Share and printer discovery</li></ul></li>
    <li>Review directory services for weak settings.</li>
    <li>Attempt credential capture and relay attacks.</li>
    <li>Escalate privileges on reachable hosts.
      <ul><li>Local misconfiguration checks</li><li>Missing patch review</li></ul></li>
    <li>Move laterally toward critical systems.</li>
    <li>Test segmentation between network zones.</li>
    <li>Search for sensitive data on shares.
      <ul><li>Password files</li><li>Configuration backups</li></ul></li>
    <li>Record the full attack path with evidence.</li>
    <li>Remove all test accounts and tools.</li>
    <li>Confirm systems returned to normal state.</li>
    <li>Draft findings for the phase report.</li>
  </ol>
  <div class="footer"><span>Page 9</span><b>northgateassurance.example</b></div>
</section>

<section class="page col-r r5">
  <div class="sub">Client <span>Obligations</span></div>
  <p>The client agrees to supply a workspace and network port for on-site testing, and to grant building access to consultants for the agreed dates.</p>
  <p>Any delays caused by missing access may extend the schedule.</p>
  <div class="sub">Pricing <span>Schedule</span></div>
  <ul><li>Fees are fixed for the scope described in this document.</li><li>Invoices are issued at the start and on delivery of the final report.</li></ul>
  <div class="footer"><span>Page 10</span><b>northgateassurance.example</b></div>
</section>

</body>
</html>
```